Stylish Business Cards Wanted

- DOUBLE SIDED Design Required -

High end, edgy cards for a corporate and personal stylist. Must include logo,
Name: Belinda Harwick
Title: Director and Stylist
telephone : +61 8 7142 5809
email: belinda@theloombriefing.example
website: theloombriefing.example
Tag: Corporate Workwear & Uniform Specialist | Personal Stylist
Would like nice icons for telephone, email, website

Target Market(s)

Businesses wanting stylish uniforms, people wanting stylish wardrobes

Industry/Entity Type

Corporate Workwear Stylist

Contact Information for Business Card

I would like black, white and gold foiling incorporated in the design - possibly a touch of the other colours on my branding guide attached Name: Belinda Harwick Title: Director and Stylist telephone : +61 8 7142 5809 email: belinda@theloombriefing.example website: theloombriefing.example Tag: Corporate Workwear & Uniform Specialist | Personal Stylist Would like nice icons for telephone, email, website

Font styles to use
Other font styles liked:
• Raleway

Colors

Designer to choose colors to be used in the design.

Requirements
Must have
• Gold foil accents

```html
<!DOCTYPE html>
<html lang="en">
<head>
<meta charset="utf-8">
<title>The Loom Briefing — Business Cards</title>
<link rel="stylesheet" href="https://fonts.googleapis.com/css2?family=Montserrat:wght@400;500;600;700&display=swap">
<style>
  :root {
    --backdrop: #1b1b1b;
    --card: #242424;
    --ink-light: #ffffff;
    --ink-soft: #e6e6e6;
    --accent: #e0136f;
    --ghost: #2c2c2c;
  }
  * { box-sizing: border-box; margin: 0; padding: 0; }
  html, body { width: 1200px; height: 988px; overflow: hidden; }
  body {
    background: var(--backdrop);
    font-family: "Montserrat", sans-serif;
    position: relative;
  }
  .card {
    position: absolute;
    left: 280px;
    width: 640px;
    height: 380px;
    background: var(--card);
    border-bottom: 6px solid var(--accent);
    border-left: 3px solid var(--accent);
    overflow: hidden;
  }
  .card--front { top: 70px; }
  .card--back { top: 520px; }

  .brand-name {
    color: var(--ink-light);
    font-weight: 600;
    letter-spacing: 0.02em;
    display: flex;
    align-items: center;
    gap: 12px;
  }
  .brand-name__dot {
    width: 14px; height: 14px;
    background: var(--accent);
    border-radius: 50%;
    flex: none;
  }
  .card--front .brand-name {
    position: absolute;
    top: 130px; left: 0; right: 0;
    justify-content: center;
    font-size: 40px;
  }
  .tagline {
    position: absolute;
    left: 0; right: 0; top: 300px;
    text-align: center;
    color: var(--accent);
    font-size: 16px;
    font-weight: 500;
    letter-spacing: 0.01em;
  }

  .card--back .brand-name {
    position: absolute;
    top: 52px; left: 44px;
    font-size: 26px;
  }
  .ghost-mark {
    position: absolute;
    right: -30px; top: 70px;
    color: var(--ghost);
    font-size: 92px;
    font-weight: 700;
    line-height: 0.95;
    text-align: right;
    white-space: nowrap;
  }
  .edge-tab {
    position: absolute;
    right: -18px; top: 44px;
    width: 36px; height: 36px;
    border-radius: 50%;
    background: var(--accent);
  }
  .person {
    position: absolute;
    right: 40px; top: 46px;
    text-align: right;
  }
  .person__name {
    color: var(--accent);
    font-size: 24px;
    font-weight: 700;
    letter-spacing: 0.02em;
    text-transform: uppercase;
  }
  .person__title {
    color: var(--ink-soft);
    font-size: 15px;
    margin-top: 4px;
  }
  .contact {
    position: absolute;
    left: 44px; bottom: 34px;
    list-style: none;
  }
  .contact__item {
    display: flex;
    align-items: center;
    gap: 12px;
    color: var(--ink-soft);
    font-size: 16px;
    margin-top: 8px;
  }
  .contact__item--phone { font-size: 24px; font-weight: 600; color: var(--ink-light); }
  .contact__icon { width: 18px; height: 18px; flex: none; fill: var(--accent); }
</style>
</head>
<body>

  <section class="card card--front" aria-label="Card front">
    <div class="brand-name"><span class="brand-name__dot"></span>The Loom Briefing</div>
    <p class="tagline">Corporate Workwear &amp; Uniform Specialist | Personal Stylist</p>
  </section>

  <section class="card card--back" aria-label="Card back">
    <div class="ghost-mark" aria-hidden="true">The Loom<br>Briefing</div>
    <span class="edge-tab"></span>

    <div class="brand-name">The Loom Briefing</div>

    <div class="person">
      <p class="person__name">Belinda Harwick</p>
      <p class="person__title">Director and Stylist</p>
    </div>

    <ul class="contact">
      <li class="contact__item contact__item--phone">
        <svg class="contact__icon" viewBox="0 0 24 24" aria-hidden="true"><path d="M6.6 10.8a15.1 15.1 0 0 0 6.6 6.6l2.2-2.2a1 1 0 0 1 1-.25 11.4 11.4 0 0 0 3.6.57 1 1 0 0 1 1 1V20a1 1 0 0 1-1 1A17 17 0 0 1 3 4a1 1 0 0 1 1-1h3.5a1 1 0 0 1 1 1c0 1.25.2 2.45.57 3.57a1 1 0 0 1-.25 1z"/></svg>
        +61 8 7142 5809
      </li>
      <li class="contact__item">
        <svg class="contact__icon" viewBox="0 0 24 24" aria-hidden="true"><path d="M2 5h20v14H2z M4 7v.5l8 5.5 8-5.5V7l-8 5.5z" fill-rule="evenodd"/></svg>
        belinda@theloombriefing.example
      </li>
      <li class="contact__item">
        <svg class="contact__icon" viewBox="0 0 24 24" aria-hidden="true"><path d="M12 2a10 10 0 1 0 0 20 10 10 0 0 0 0-20zm6.9 6h-3a15 15 0 0 0-1.3-3.9A8 8 0 0 1 18.9 8zM12 4c.8 1.2 1.5 2.5 1.9 4h-3.8c.4-1.5 1.1-2.8 1.9-4zM4.3 14a8 8 0 0 1 0-4h3.4a16 16 0 0 0 0 4zm.8 2h3a15 15 0 0 0 1.3 3.9A8 8 0 0 1 5.1 16zm3-8h-3a8 8 0 0 1 4.3-3.9A15 15 0 0 0 8.1 8zM12 20c-.8-1.2-1.5-2.5-1.9-4h3.8c-.4 1.5-1.1 2.8-1.9 4zm2.3-6H9.7a14 14 0 0 1 0-4h4.6a14 14 0 0 1 0 4zm.3 5.9a15 15 0 0 0 1.3-3.9h3a8 8 0 0 1-4.3 3.9zm1.7-5.9a16 16 0 0 0 0-4h3.4a8 8 0 0 1 0 4z"/></svg>
        www.theloombriefing.example
      </li>
    </ul>
  </section>

</body>
</html>
```